Smile club flyer design

I am launching an office smile club and would like a design that sits my branding and that is appealing to customers. I have a design (I need a new one) that has all the information.
My website is maplehavendentalcarekx.com
Brand color is green. The design can be any color

Target Market(s)

Ages 30+

Industry/Entity Type

Dental

Font styles to use
Serif

Requirements
Must have
• Appealing to patients

```html
<!DOCTYPE html>
<html lang="en">
<head>
<meta charset="utf-8">
<title>Smile Club Membership – Maplehaven Dental Care</title>
<link rel="stylesheet" href="https://fonts.googleapis.com/css2?family=Allura&family=Bebas+Neue&family=Montserrat:ital,wght@0,700;1,800&family=Playfair+Display:wght@700&family=Roboto+Condensed:wght@400;700&family=Tinos&display=swap">
<style>
  :root {
    --backdrop: #00260f;
    --mint-bg: #e3f9ec;
    --mint-soft: #d6fde4;
    --mint-bright: #b3fbd0;
    --green: #0a8d3e;
    --green-deep: #08702f;
    --ink: #0a0a0a;
    --grey: #5a5a5a;
    --card-bg: #f1fdf5;
    --white: #ffffff;
  }
  * { box-sizing: border-box; margin: 0; padding: 0; }
  html, body { width: 924px; height: 1200px; overflow: hidden; }
  body { background: var(--backdrop); position: relative; }

  .flyer {
    position: absolute; left: 62px; top: 0;
    width: 1049px; height: 1572px;
    transform: scale(0.7634); transform-origin: 0 0;
    background: linear-gradient(180deg, var(--mint-bg), #e8fbef 60%, var(--mint-soft));
    overflow: hidden;
    font-family: "Roboto Condensed", sans-serif;
    color: var(--ink);
  }
  .flyer-bg { position: absolute; inset: 0; width: 1049px; height: 1572px; }

  .brand { position: absolute; top: 44px; left: 0; width: 100%; text-align: center; color: var(--green); font-family: "Playfair Display", serif; font-weight: 700; }
  .brand-name { font-size: 66px; line-height: 70px; letter-spacing: -0.5px; }
  .brand-sub { font-size: 30px; letter-spacing: 10px; line-height: 36px; display: flex; justify-content: center; align-items: center; gap: 14px; }
  .brand-sub::before, .brand-sub::after { content: ""; width: 44px; height: 3px; background: var(--green); }

  .headline { position: absolute; left: 0; width: 100%; text-align: center; white-space: nowrap; }
  .intro { top: 186px; font-family: "Allura", cursive; font-size: 72px; line-height: 1; color: var(--ink); z-index: 2; }
  .club { top: 229px; font-family: "Bebas Neue", sans-serif; font-weight: 400; font-size: 126px; line-height: 1; color: var(--green); -webkit-text-stroke: 1.5px var(--green); }
  .membership { top: 343px; font-family: "Bebas Neue", sans-serif; font-weight: 400; font-size: 132px; line-height: 1; color: var(--ink); -webkit-text-stroke: 3px var(--ink); }
  .tagline { top: 487px; font-weight: 700; font-size: 24px; letter-spacing: 0.2px; }

  .plan { position: absolute; width: 287px; background: var(--card-bg); box-shadow: 0 3px 8px rgba(0,0,0,0.18); }
  .plan-core { left: 70px; top: 714px; height: 383px; }
  .plan-bright { left: 380px; top: 714px; height: 383px; }
  .plan-total { left: 691px; top: 714px; height: 383px; }
  .plan-refresh { left: 74px; top: 1189px; height: 298px; }
  .plan-head { position: absolute; top: 0; left: 0; width: 287px; height: 130px; }
  .plan-title { position: absolute; top: 10px; width: 100%; text-align: center; color: var(--white); font-family: "Tinos", serif; white-space: nowrap; }
  .plan-title b { display: block; font-weight: 400; font-size: 32px; line-height: 34px; letter-spacing: 0.5px; }
  .plan-title span { display: block; font-size: 24px; line-height: 26px; }
  .price {
    position: absolute; top: 77px; left: 95px; width: 96px; height: 96px; border-radius: 50%;
    border: 4px solid var(--white); background: var(--green); color: var(--white);
    font-family: "Bebas Neue", sans-serif; text-align: center; padding-top: 12px;
  }
  .plan-bright .price, .plan-refresh .price { background: var(--green-deep); }
  .price strong { display: block; font-weight: 400; font-size: 48px; line-height: 42px; }
  .price small { display: block; font-size: 18px; line-height: 18px; }
  .plan-refresh .price strong { font-size: 50px; line-height: 66px; }

  .perks { position: absolute; top: 199px; left: 48px; right: 0; list-style: none; font-size: 16px; line-height: 21px; color: #1c1c1c; white-space: nowrap; }
  .perks li { position: relative; margin-bottom: 10px; }
  .perks li::before {
    content: ""; position: absolute; left: -24px; top: 6px; width: 11px; height: 7px;
    background: var(--green); border-radius: 0 100% 0 100%;
  }
  .perks li::after {
    content: ""; position: absolute; left: -14px; top: 4px; width: 9px; height: 7px;
    background: var(--green); border-radius: 100% 0 100% 0;
  }

  .ribbon { position: absolute; left: -4px; top: -3px; width: 86px; height: 86px; }

  .financing { position: absolute; left: 420px; width: 560px; text-align: center; font-family: "Montserrat", sans-serif; white-space: nowrap; }
  .fin-title { top: 1174px; font-size: 24px; line-height: 30px; font-weight: 700; color: var(--grey); }
  .fin-partners { top: 1210px; display: flex; justify-content: center; align-items: center; gap: 30px; font-size: 44px; line-height: 54px; font-weight: 700; color: #2b2b2b; }
  .partner { display: flex; align-items: center; gap: 12px; }
  .partner::before { content: ""; width: 34px; height: 34px; border-radius: 50%; background: var(--green); }
  .partner-alt::before { background: #e0453f; }
  .fin-divider { width: 1px; height: 48px; background: #cfe3d6; }
  .fin-plans { top: 1268px; font-size: 20px; line-height: 26px; font-weight: 700; color: #6a6a6a; letter-spacing: 0.5px; }
  .fin-fee { top: 1304px; font-size: 19px; line-height: 26px; font-weight: 800; font-style: italic; color: var(--ink); }

  .cta { position: absolute; left: 410px; width: 600px; text-align: center; font-family: "Bebas Neue", sans-serif; font-weight: 400; line-height: 1; white-space: nowrap; }
  .cta-join { top: 1343px; font-size: 74px; color: var(--green); -webkit-text-stroke: 1.5px var(--green); }
  .cta-phone { top: 1422px; font-size: 83px; color: var(--ink); -webkit-text-stroke: 2px var(--ink); }
</style>
</head>
<body>
<main class="flyer">
  <svg class="flyer-bg" viewBox="0 0 1049 1572" aria-hidden="true">
    <ellipse cx="420" cy="120" rx="560" ry="530" fill="var(--mint-bright)"/>
    <ellipse cx="560" cy="60" rx="560" ry="580" fill="var(--green)"/>
    <ellipse cx="500" cy="115" rx="520" ry="525" fill="var(--mint-soft)"/>
    <ellipse cx="500" cy="1640" rx="610" ry="560" fill="var(--green)"/>
    <ellipse cx="470" cy="1650" rx="600" ry="560" fill="var(--mint-bright)"/>
    <ellipse cx="500" cy="1700" rx="560" ry="560" fill="var(--mint-soft)"/>
  </svg>

  <header class="brand">
    <div class="brand-name">Maplehaven</div>
    <div class="brand-sub">DENTAL CARE</div>
  </header>

  <p class="headline intro">Introducing</p>
  <h1 class="headline club">SMILE CLUB</h1>
  <h2 class="headline membership">MEMBERSHIP</h2>
  <p class="headline tagline">AFFORDABLE DENTAL CARE - NO INSURANCE REQUIRED</p>

  <section class="plan plan-core">
    <svg class="plan-head" viewBox="0 0 287 130"><path d="M0 0H287V55Q143.5 200 0 55Z" fill="var(--green)"/></svg>
    <div class="plan-title"><b>CORE CARE</b><span>Preventive</span></div>
    <div class="price"><strong>$39</strong><small>/MONTH</small></div>
    <ul class="perks">
      <li>Comprehensive Annual Exam</li>
      <li>2 Professional Cleanings per Year</li>
      <li>Routine Bitewing X-rays</li>
      <li>10% Savings on Treatment</li>
    </ul>
  </section>

  <section class="plan plan-bright">
    <svg class="plan-head" viewBox="0 0 287 130"><path d="M0 0H287V55Q143.5 200 0 55Z" fill="var(--green-deep)"/></svg>
    <div class="plan-title"><b>BRIGHT</b><span>Cosmetic</span></div>
    <div class="price"><strong>$59</strong><small>/MONTH</small></div>
    <ul class="perks">
      <li>Annual In-Office Whitening<br>(Top &amp; Bottom)</li>
      <li>Custom Whitening Trays</li>
      <li>15% Savings on Elective Treatment</li>
    </ul>
  </section>

  <section class="plan plan-total">
    <svg class="plan-head" viewBox="0 0 287 130"><path d="M0 0H287V55Q143.5 200 0 55Z" fill="var(--green)"/></svg>
    <div class="plan-title"><b>TOTAL SMILE</b><span>Periodontal</span></div>
    <div class="price"><strong>$89</strong><small>/MONTH</small></div>
    <ul class="perks">
      <li>3-4 Perio Maintenance Visits<br>per Year</li>
      <li>1 Comprehensive Exam</li>
      <li>Diagnostic X-rays</li>
      <li>15% Savings on Restorative &amp;<br>Elective Care</li>
    </ul>
  </section>

  <section class="plan plan-refresh">
    <svg class="plan-head" viewBox="0 0 287 130"><path d="M0 0H287V55Q143.5 200 0 55Z" fill="var(--green-deep)"/></svg>
    <svg class="ribbon" viewBox="0 0 86 86">
      <polygon points="0,56 56,0 76,0 0,78" fill="var(--green)"/>
      <text x="25" y="41" transform="rotate(-45 25 41)" text-anchor="middle" font-family="Tinos, serif" font-size="15" fill="#fff">NEW</text>
    </svg>
    <div class="plan-title"><b>SMILE</b><span>Refresh Package</span></div>
    <div class="price"><strong>$499</strong></div>
    <ul class="perks">
      <li>Cleaning + Comprehensive Exam +<br>Whitening</li>
      <li>Limited Time Offer</li>
    </ul>
  </section>

  <p class="financing fin-title">FLEXIBLE FINANCING FOR TREATMENTS</p>
  <div class="financing fin-partners">
    <span class="partner">FlexPay</span>
    <span class="fin-divider"></span>
    <span class="partner partner-alt">Plumline</span>
  </div>
  <p class="financing fin-plans">PAYMENT PLANS AVAILABLE</p>
  <p class="financing fin-fee">*$49 Lifetime Activation Fee (Non-refundable)</p>

  <p class="cta cta-join">JOIN SMILE CLUB TODAY!</p>
  <p class="cta cta-phone">865-555-0148</p>
</main>
</body>
</html>
```